A new updated business card. A good first impression for new customers to our business.

I need something unique. I will attached a picture of our old rubbish cards, and also our current Logo ( I think this needs an update if you have any ideas, its very basic and budget)The best way you will get to see my business is checking our Facebook page, I don't really know what else to say, but anything you want to know, ask away.www.facebook.com/tkwashandseal/

Target Market(s)

Home owners

Industry/Entity Type

Business

Contact Information for Business Card

T&K's Pressure Cleaning & Concrete Sealing
Maya 0492 615 370 maya@tkwashandseal.com
Dylan 0431 528 906 dylan@tkwashandseal.com

FB: www.facebook.com/tkwashandseal/
Website: www.tkwashandseal.net (This is pretty rubbish- we don't really use it)

100% customer satisfaction guaranteed

All aspects of Hi-Pressure Cleaning
Sealing & Re-Sealing
Roof Cleaning
Colour sealing
Decorative coatings

Free no obligation quotes

Requirements
Must have
• NO OBLIGATION FREE quotes
• 100% Customer satisfaction guaranteed
• Can you please add both names, contact details and email address on one card.
• Dylan 0431 528 906
• dylan@tkwashandseal.com
• Maya 0492 615 370
• maya@tkwashandseal.com
• Please change the services:
• Hot/Cold Hi-Pressure Cleaning
• Sealing & Re-Sealing
• Roof Cleaning
• Colour Sealing
• Decorative Coatings
• Concrete Honing
• Thanks
Nice to have
• Something a bit different, something eye catching.l

```html
<!DOCTYPE html>
<html lang="en">
<head>
<meta charset="UTF-8">
<title>T&amp;K's Pressure Cleaning &amp; Concrete Sealing – Business Card</title>
<link href="https://fonts.googleapis.com/css2?family=Open+Sans:wght@400;600;700&display=swap" rel="stylesheet">
<style>
  :root {
    --page: #d9d9d9;
    --card: #050505;
    --ink: #ffffff;
    --accent-blue: #3fb6e8;
    --accent-red: #e3262b;
    --rule: #2a2a2a;
    --badge: #ffffff;
  }
  * { box-sizing: border-box; margin: 0; padding: 0; }
  html, body {
    width: 1200px; height: 900px; overflow: hidden;
    background: var(--page);
    font-family: "Open Sans", Arial, sans-serif;
  }
  .sheet {
    width: 1200px; height: 900px;
    display: flex; align-items: center; justify-content: center; gap: 40px;
  }
  .card {
    position: relative;
    width: 540px; height: 310px;
    background: var(--card);
    border-radius: 18px;
    color: var(--ink);
    box-shadow: 0 6px 18px rgba(0,0,0,.25);
    overflow: hidden;
  }
  .brand {
    position: absolute;
    display: flex; align-items: center; gap: 10px;
  }
  .brand-dot {
    flex: none; width: 14px; height: 14px; border-radius: 50%;
    background: var(--accent-blue);
  }
  .brand-name {
    font-weight: 700; font-size: 17px; line-height: 1.25;
    color: var(--ink); text-transform: uppercase; letter-spacing: .5px;
  }
  /* front */
  .card--front .brand { left: 28px; top: 112px; width: 220px; }
  .divider {
    position: absolute; left: 262px; top: 30px; bottom: 30px;
    width: 1px; background: var(--rule);
  }
  .contacts { position: absolute; left: 284px; top: 40px; right: 20px; }
  .person { margin-bottom: 16px; }
  .person-name {
    color: var(--accent-blue); font-weight: 700; font-size: 17px; margin-bottom: 4px;
  }
  .line {
    display: flex; align-items: center; gap: 10px;
    font-size: 13px; line-height: 21px;
  }
  .line svg { flex: none; width: 12px; height: 12px; }
  .online { margin-top: 8px; }
  /* back */
  .card--back .brand { left: 28px; top: 118px; width: 230px; }
  .services {
    position: absolute; left: 282px; top: 32px;
    list-style: none; font-size: 13px; line-height: 22px;
  }
  .services li { display: flex; align-items: center; gap: 9px; }
  .services li::before {
    content: ""; width: 7px; height: 7px; border-radius: 50%;
    background: var(--accent-blue); flex: none;
  }
  .guarantee-badge {
    position: absolute; left: 330px; top: 180px;
    width: 84px; height: 54px; background: var(--badge);
  }
  .free-quotes {
    position: absolute; left: 282px; right: 20px; top: 250px;
    font-size: 13px; font-weight: 700; line-height: 20px;
    color: var(--accent-blue); text-transform: uppercase; letter-spacing: .3px;
  }
</style>
</head>
<body>
<main class="sheet">

  <section class="card card--front" aria-label="Business card front">
    <div class="brand">
      <span class="brand-dot"></span>
      <span class="brand-name">T&amp;K's Pressure Cleaning &amp; Concrete Sealing</span>
    </div>
    <div class="divider"></div>
    <div class="contacts">
      <div class="person">
        <p class="person-name">Maya</p>
        <p class="line">
          <svg viewBox="0 0 12 12" aria-hidden="true"><path d="M2 1h2.5l1 3-1.5 1a7 7 0 0 0 3 3l1-1.5 3 1V11c-5 0-9-4-9-9z" fill="#e3262b"/></svg>
          0492 615 370
        </p>
        <p class="line">
          <svg viewBox="0 0 12 12" aria-hidden="true"><rect x="1" y="2.5" width="10" height="7" fill="#e3262b"/><path d="M1 2.5l5 4 5-4" stroke="#050505" fill="none"/></svg>
          maya@tkwashandseal.com
        </p>
      </div>
      <div class="person">
        <p class="person-name">Dylan</p>
        <p class="line">
          <svg viewBox="0 0 12 12" aria-hidden="true"><path d="M2 1h2.5l1 3-1.5 1a7 7 0 0 0 3 3l1-1.5 3 1V11c-5 0-9-4-9-9z" fill="#e3262b"/></svg>
          0431 528 906
        </p>
        <p class="line">
          <svg viewBox="0 0 12 12" aria-hidden="true"><rect x="1" y="2.5" width="10" height="7" fill="#e3262b"/><path d="M1 2.5l5 4 5-4" stroke="#050505" fill="none"/></svg>
          dylan@tkwashandseal.com
        </p>
      </div>
      <div class="online">
        <p class="line">
          <svg viewBox="0 0 12 12" aria-hidden="true"><circle cx="6" cy="6" r="4" fill="#e3262b"/></svg>
          tkwashandseal
        </p>
        <p class="line">
          <svg viewBox="0 0 12 12" aria-hidden="true"><circle cx="6" cy="6" r="5" fill="#e3262b"/><path d="M1 6h10M6 1c-2.5 3-2.5 7 0 10M6 1c2.5 3 2.5 7 0 10" stroke="#050505" stroke-width=".9" fill="none"/></svg>
          www.tkwashandseal.net
        </p>
      </div>
    </div>
  </section>

  <section class="card card--back" aria-label="Business card back">
    <div class="brand">
      <span class="brand-dot"></span>
      <span class="brand-name">T&amp;K's Pressure Cleaning &amp; Concrete Sealing</span>
    </div>
    <ul class="services">
      <li>Hot/Cold Hi-Pressure Cleaning</li>
      <li>Sealing &amp; Re-Sealing</li>
      <li>Roof Cleaning</li>
      <li>Colour Sealing</li>
      <li>Decorative Coatings</li>
      <li>Concrete Honing</li>
    </ul>
    <div class="guarantee-badge" role="img" aria-label="100% customer satisfaction guaranteed badge"></div>
    <p class="free-quotes">No obligation free quotes</p>
  </section>

</main>
</body>
</html>
```